New Business Card Design Project

Need a design that will create an impact / strong impression towards our clients for our business. We are in the lighting business and we do lighting retrofits for large commercial to industrial clientele.

Target Market(s)

Lighting Industry

Industry/Entity Type

Business

Font styles to use
Other font styles liked:
• we would like to use the font on our logo, not sure what it is though..

Requirements
Must have
• Our logo.
Nice to have
• We are open to suggestions that have to do with lighting.

```html
<!DOCTYPE html>
<html lang="en">
<head>
<meta charset="utf-8">
<title>Lumarc Business Card</title>
<link href="https://fonts.googleapis.com/css2?family=Montserrat:wght@600;700&family=PT+Sans:wght@400&display=swap" rel="stylesheet">
<style>
  :root {
    --stage: #232323;
    --paper: #ffffff;
    --brand-green: #0b8234;
    --brand-dark: #1b4d2a;
    --accent-green: #2e8b3a;
    --rule-green: #9fd38f;
    --ink: #222222;
    --tile-faint: rgba(255, 255, 255, 0.13);
    --tile-bright: #ffffff;
  }
  * { margin: 0; padding: 0; box-sizing: border-box; }
  html, body {
    width: 1200px;
    height: 900px;
    overflow: hidden;
    background: var(--stage);
  }
  .stage {
    position: relative;
    width: 1200px;
    height: 900px;
  }
  .card {
    position: absolute;
    top: 306px;
    width: 440px;
    height: 271px;
    overflow: hidden;
  }
  .card-front { left: 149px; background: var(--paper); }
  .card-back { left: 608px; background: var(--brand-green); }

  .brand {
    position: absolute;
    right: 23px;
    top: 58px;
    display: flex;
    align-items: center;
    gap: 10px;
    font-family: "Montserrat", sans-serif;
    font-weight: 700;
    font-size: 34px;
    letter-spacing: 1px;
    color: var(--brand-dark);
  }
  .brand-square {
    width: 22px;
    height: 22px;
    background: var(--accent-green);
  }

  .person {
    position: absolute;
    left: 24px;
    top: 153px;
    right: 23px;
  }
  .person-name-row {
    display: flex;
    align-items: center;
  }
  .person-name {
    font-family: "Montserrat", sans-serif;
    font-weight: 600;
    font-size: 14.5px;
    color: var(--brand-green);
    white-space: nowrap;
  }
  .person-rule {
    flex: 1;
    height: 1px;
    background: var(--rule-green);
    margin-left: 2px;
  }
  .person-title {
    font-family: "PT Sans", sans-serif;
    font-size: 12px;
    color: var(--ink);
    margin-top: 1px;
  }

  .contact-list {
    position: absolute;
    left: 24px;
    top: 198px;
    list-style: none;
    font-family: "PT Sans", sans-serif;
    font-size: 12.5px;
    color: var(--ink);
  }
  .contact-list li {
    display: flex;
    align-items: center;
    height: 16px;
  }
  .contact-icon {
    width: 9px;
    height: 9px;
    margin-right: 6px;
    fill: var(--brand-green);
  }
  .address {
    position: absolute;
    right: 23px;
    top: 214px;
    text-align: right;
    font-family: "PT Sans", sans-serif;
    font-size: 12.5px;
    line-height: 16px;
    color: var(--ink);
  }

  .tile-grid {
    position: absolute;
    inset: 0;
    display: grid;
    grid-template-columns: repeat(3, 150px);
    grid-template-rows: repeat(5, 55px);
    padding: 10px 0 0 5px;
  }
  .tile {
    display: flex;
    align-items: center;
    justify-content: center;
    font-family: "Montserrat", sans-serif;
    font-weight: 700;
    font-size: 20px;
    letter-spacing: 1px;
    color: var(--tile-faint);
  }
  .tile-bright { color: var(--tile-bright); }
</style>
</head>
<body>
<main class="stage">
  <section class="card card-front" aria-label="Card front">
    <div class="brand">
      <span class="brand-name">LUMARC</span>
      <span class="brand-square"></span>
    </div>

    <div class="person">
      <div class="person-name-row">
        <h1 class="person-name">JONATHAN SMITH</h1>
        <span class="person-rule"></span>
      </div>
      <p class="person-title">Managing Director</p>
    </div>

    <ul class="contact-list">
      <li>
        <svg class="contact-icon" viewBox="0 0 10 10"><path d="M2 0.5 L3.6 2.6 L2.8 3.6 Q4 6 6.4 7.2 L7.4 6.4 L9.5 8 L8.4 9.5 Q3.5 9 0.5 1.6 Z"/></svg>
        (044)123456789
      </li>
      <li>
        <svg class="contact-icon" viewBox="0 0 10 10"><path d="M0.5 2 H9.5 V8.5 H0.5 Z M1 2.5 L5 5.5 L9 2.5" stroke="#fff" stroke-width="0.8"/></svg>
        info@youremail.com
      </li>
      <li>
        <svg class="contact-icon" viewBox="0 0 10 10"><circle cx="5" cy="5" r="4.5"/><path d="M0.5 5 H9.5 M5 0.5 Q2.5 5 5 9.5 M5 0.5 Q7.5 5 5 9.5" stroke="#fff" stroke-width="0.7" fill="none"/></svg>
        www.websitename.com
      </li>
    </ul>

    <address class="address" style="font-style: normal;">
      1234, Address GoesHere,<br>
      Country name, 12345
    </address>
  </section>

  <section class="card card-back" aria-label="Card back">
    <div class="tile-grid">
      <span class="tile">LUMARC</span>
      <span class="tile">LUMARC</span>
      <span class="tile">LUMARC</span>
      <span class="tile">LUMARC</span>
      <span class="tile">LUMARC</span>
      <span class="tile">LUMARC</span>
      <span class="tile">LUMARC</span>
      <span class="tile tile-bright">LUMARC</span>
      <span class="tile">LUMARC</span>
      <span class="tile">LUMARC</span>
      <span class="tile">LUMARC</span>
      <span class="tile">LUMARC</span>
      <span class="tile">LUMARC</span>
      <span class="tile">LUMARC</span>
      <span class="tile">LUMARC</span>
    </div>
  </section>
</main>
</body>
</html>
```